Brintel Works - Fast, Efficient and Gas Mainteance for Domestic, Commercial and Industrial clients

We are in the process of purchasing a new business and would like to get a new logo and business card.
Business is a gas maintenance business that also does new gas installations.
Has been established since 1988.
Services include:
Install all types of gas appliances & equipment inc. hot water units
Maintain / repair / replace all types of gas appliances & equipment

Target Market(s)

Domestic, Commercial and Industrial clients

Industry/Entity Type

Business

Contact Information for Business Card

admin@brintelworks.com.au
07 3918 4726
Brintel Works PTY LTD

Logo Text

Gas Fitting & Plumbing Maintenance Specialists

Font styles to use
Sans Serif

Requirements
Must have
• Logo
• Business name, contact number, email address, web address
• Domestic | Commercial | Industrial Est Since 1988
Nice to have
• Possibly a black card with a flame logo to one side
Should not have
• Spelling errors

```html
<!DOCTYPE html>
<html lang="en">
<head>
<meta charset="utf-8">
<title>Brintel Works PTY LTD – Business Card</title>
<link href="https://fonts.googleapis.com/css2?family=Open+Sans:wght@400;700&family=Tinos&family=Allura&display=swap" rel="stylesheet">
<style>
  :root{
    --stage:#ece9e4;
    --slate:#3b4250;
    --slate-deep:#2f3541;
    --flame:#e5533d;
    --paper:#f3f3f3;
    --ink:#3a3f4a;
    --muted:#7a7f88;
    --white:#ffffff;
  }
  *{margin:0;padding:0;box-sizing:border-box}
  html,body{width:1200px;height:902px;overflow:hidden;background:var(--stage)}
  .canvas{position:relative;width:1200px;height:902px}
  .card{position:absolute;left:240px;width:720px;height:411px;border-radius:6px;overflow:hidden;box-shadow:0 6px 18px rgba(0,0,0,.18)}
  .card--back{top:30px;background:linear-gradient(160deg,#46505f,var(--slate-deep))}
  .card--front{top:461px;background:var(--paper)}
  .card svg.wave{position:absolute;inset:0;width:720px;height:411px}

  .brand{font-family:"Open Sans",sans-serif;font-weight:700;color:var(--flame);text-transform:uppercase;letter-spacing:1px;white-space:nowrap}
  .brand-suffix{font-family:"Open Sans",sans-serif;font-weight:700;font-size:10px;letter-spacing:.5px}
  .tagline{font-family:"Open Sans",sans-serif;font-weight:700;white-space:nowrap}

  /* back face */
  .back-lockup{position:absolute;left:0;right:0;top:140px;text-align:center}
  .back-lockup .brand{font-size:50px}
  .back-lockup .brand-suffix{color:var(--white);vertical-align:top;margin-left:6px;position:relative;top:10px}
  .back-lockup .tagline{color:#e6e8ec;font-size:26px;margin-top:4px}

  /* front face */
  .front-lockup{position:absolute;left:110px;top:50px}
  .front-lockup .brand{font-size:38px}
  .front-lockup .brand-suffix{color:var(--ink);vertical-align:top;margin-left:6px;position:relative;top:6px}
  .front-lockup .tagline{color:var(--ink);font-size:20px}
  .sectors{display:flex;align-items:baseline;gap:14px;margin-top:6px;white-space:nowrap}
  .sectors-list{font-family:"Open Sans",sans-serif;font-size:12px;color:var(--muted)}
  .established{font-family:"Allura",cursive;font-size:26px;color:var(--muted)}

  .product-shot{position:absolute;left:500px;top:168px;width:196px;height:186px;border-radius:4px;
    background:radial-gradient(circle at 35% 60%,#d9572a 0 18%,transparent 19%),linear-gradient(135deg,#b9bdc2,#55585e)}

  .contacts{position:absolute;left:44px;top:304px;list-style:none}
  .contacts li{display:flex;align-items:center;gap:12px;font-family:"Tinos",serif;font-size:20px;color:var(--white);line-height:33px;white-space:nowrap}
  .contacts li:first-child{font-size:24px}
  .contact-icon{width:18px;height:18px;flex:none}
</style>
</head>
<body>
<main class="canvas">

  <section class="card card--back" aria-label="Card back">
    <div class="back-lockup">
      <div class="brand">Brintel Works<span class="brand-suffix">PTY LTD</span></div>
      <div class="tagline">Gas fitting &amp; Plumbing Specialists</div>
    </div>
  </section>

  <section class="card card--front" aria-label="Card front">
    <svg class="wave" viewBox="0 0 720 411" aria-hidden="true">
      <path d="M0,282 C190,300 320,270 420,196 C510,130 610,108 720,100 L720,411 L0,411 Z" fill="var(--flame)"/>
      <path d="M0,298 C200,316 330,286 430,212 C520,146 615,124 720,116 L720,411 L0,411 Z" fill="var(--slate)"/>
    </svg>

    <div class="front-lockup">
      <div class="brand">Brintel Works<span class="brand-suffix">PTY LTD</span></div>
      <div class="tagline">Gas fitting &amp; Plumbing Specialists</div>
      <div class="sectors">
        <span class="sectors-list">Domestic | Commercial | Industrial</span>
        <span class="established">Est Since 1988</span>
      </div>
    </div>

    <div class="product-shot" role="img" aria-label="Photo of a gas log heater with fire and two hot water units"></div>

    <ul class="contacts">
      <li>
        <svg class="contact-icon" viewBox="0 0 18 18" aria-hidden="true"><rect width="18" height="18" rx="3" fill="#e9eaec"/><path d="M5 5c0 5 3 8 8 8l1-2-2-1-1 1c-2-1-3-2-4-4l1-1-1-2z" fill="var(--slate)"/></svg>
        07 3918 4726
      </li>
      <li>
        <svg class="contact-icon" viewBox="0 0 18 18" aria-hidden="true"><rect width="18" height="18" rx="3" fill="#e9eaec"/><rect x="4" y="5.5" width="10" height="7" fill="none" stroke="var(--slate)" stroke-width="1.2"/><path d="M4 5.5l5 4 5-4" fill="none" stroke="var(--slate)" stroke-width="1.2"/></svg>
        admin@brintelworks.com.au
      </li>
      <li>
        <svg class="contact-icon" viewBox="0 0 18 18" aria-hidden="true"><rect width="18" height="18" rx="3" fill="#e9eaec"/><circle cx="9" cy="9" r="5" fill="none" stroke="var(--slate)" stroke-width="1.2"/><path d="M4 9h10M9 4c-2.5 3-2.5 7 0 10M9 4c2.5 3 2.5 7 0 10" fill="none" stroke="var(--slate)" stroke-width="1"/></svg>
        www.brintelworks.com.au
      </li>
    </ul>
  </section>

</main>
</body>
</html>
```